Timber Ridge Athletics Web Design

Need to completely update website - simple and clean look - informative
this will be our main source for booking appointments etc. needs to have baseball and softball content. we currently have a site - looking to update - we would like you to design and add to our current site.

Target Market(s)

ages 15-45, youth and parents for kids- softball and baseball players /fitness

Industry/Entity Type

baseball and softball indoor training facility

Coding

Coded - Design and coding required

Number of Pages Required

5+ page

Colors

Designer to choose colors to be used in the design.

Requirements
Must have
• our colors of business are green and black- we need you to completely set up the website for us
Nice to have
• out current webiste is www.timberridge482.example

```html
<!DOCTYPE html>
<html lang="en">
<head>
<meta charset="utf-8">
<title>Timber Ridge Athletics – Baseball and Softball</title>
<link rel="stylesheet" href="https://fonts.googleapis.com/css2?family=Montserrat:wght@500;600;700;800&family=Arimo:wght@400;700&display=swap">
<style>
:root{
  --green:#3cf01c;
  --black:#000;
  --panel:#1b1b1b;
  --white:#fff;
  --grey:#c9c9c9;
}
*{box-sizing:border-box;margin:0;padding:0}
html,body{width:1200px;height:4415px;overflow:hidden;background:var(--black)}
body{position:relative;font-family:"Arimo",Arial,sans-serif;color:var(--white)}
a{text-decoration:none}
.abs{position:absolute}
.heading{font-family:"Montserrat",Arial,sans-serif;font-weight:800;text-transform:uppercase;letter-spacing:.5px}
.rule{width:56px;height:5px;background:var(--green)}
.body-text{font-size:13px;line-height:25.7px;text-align:justify}
.btn{display:flex;align-items:center;justify-content:center;font-family:"Montserrat",Arial,sans-serif;font-weight:700;text-transform:uppercase;border-radius:40px;font-size:14px}
.btn-solid{background:var(--green);color:var(--black)}
.btn-line{border:2px solid var(--green);color:var(--white)}
.brand{display:flex;align-items:center;gap:12px}
.brand-mark{width:70px;height:70px;border-radius:50%;border:4px solid var(--green);background:var(--black)}
.brand-name{font-family:"Montserrat",Arial,sans-serif;font-weight:700;font-size:23px;color:var(--white);line-height:1.1;text-transform:uppercase}
.nav{display:flex;gap:31px;font-family:"Montserrat",Arial,sans-serif;font-weight:600;font-size:13.5px;text-transform:uppercase}

.site-header{left:0;top:0;width:1200px;height:118px;background:var(--black)}
.main-nav{left:0;top:118px;width:1200px;height:60px;background:var(--green);color:var(--black);align-items:center;padding-left:125px}

.hero{left:0;top:178px;width:1200px;height:682px;
  background:
    radial-gradient(ellipse 420px 260px at 880px 420px,rgba(150,160,150,.35),transparent 70%),
    radial-gradient(ellipse 600px 200px at 600px 80px,rgba(120,130,120,.35),transparent 70%),
    linear-gradient(180deg,#1b201b 0%,#2c332b 35%,#35453a 62%,#1f2a20 85%,#0b0e0b 100%)}
.hero-title{left:0;width:1200px;top:262px;text-align:center;font-size:74px;color:var(--green)}
.hero-sub{left:0;width:1200px;top:360px;text-align:center;font-size:37px;font-weight:700}
.dots{left:575px;top:657px;display:flex;gap:6px}
.dots span{width:11px;height:11px;border-radius:50%;background:var(--white)}
.dots span.on{background:var(--green)}

.team-card{top:2185px;width:311px;height:455px;background:var(--panel)}
.team-photo{left:0;top:0;width:311px;height:275px}
.team-name{left:0;width:311px;top:295px;text-align:center;font-size:23px;color:var(--green);font-weight:700}
.team-role{left:40px;width:231px;top:340px;text-align:center;font-size:12.5px;line-height:25.7px;color:var(--grey)}

.camp-card{width:470px;height:235px;background:var(--panel)}
.camp-photo{left:10px;top:12px;width:210px;height:211px}
.camp-title{left:216px;top:20px;width:236px;font-family:"Montserrat",Arial,sans-serif;font-weight:700;font-size:18px;line-height:29px;color:var(--green)}
.camp-text{left:218px;top:92px;width:234px;font-size:12.5px;line-height:25.7px;color:var(--grey);text-align:justify}
.camp-more{left:220px;top:182px;font-family:"Montserrat",Arial,sans-serif;font-weight:700;font-size:13px;color:var(--green)}

.footer-nav{left:0;width:1200px;top:4165px;justify-content:center;gap:31px}
.divider{left:112px;width:976px;height:1px;background:#333}
.contact{display:flex;align-items:center;gap:18px;font-size:14.5px;line-height:24px}
.contact-icon{width:46px;height:46px;border-radius:50%;border:1.5px solid var(--white);display:flex;align-items:center;justify-content:center;flex:none}
.social{width:38px;height:38px;border-radius:50%;border:1.5px solid var(--white)}
</style>
</head>
<body>

<header class="site-header abs">
  <div class="brand abs" style="left:110px;top:24px">
    <div class="brand-mark"></div>
    <div class="brand-name">Timber Ridge<br><span style="font-size:12px;color:var(--green);letter-spacing:2px">Baseball and Softball</span></div>
  </div>
  <a class="btn btn-line abs" style="left:693px;top:32px;width:162px;height:50px;font-size:13.5px">Client Login</a>
  <a class="btn btn-solid abs" style="left:867px;top:32px;width:222px;height:50px;font-size:13.5px">Book Appointments</a>
</header>
<nav class="main-nav nav abs">
  <span>Home</span><span>About Us</span><span>Our Facility</span><span>Lessons</span><span>Team Rental Pricing</span><span>Instructor Opportunities</span><span>Camps/Classes</span>
</nav>

<section class="hero abs" role="img" aria-label="Indoor batting cage with netting and scattered baseballs in a dim training facility">
  <h1 class="hero-title heading abs">Timber Ridge 482</h1>
  <p class="hero-sub heading abs">Baseball and Softball</p>
  <a class="btn btn-solid abs" style="left:497px;top:432px;width:206px;height:62px;font-size:18px">Get Started</a>
  <div class="dots abs"><span></span><span class="on"></span><span></span></div>
</section>

<section class="about">
  <div class="abs" style="left:143px;top:953px;width:434px;height:434px;border-radius:50%;background:var(--green);display:flex;align-items:center;justify-content:center">
    <div style="width:400px;height:400px;border-radius:50%;background:var(--white);display:flex;align-items:center;justify-content:center">
      <div style="width:372px;height:372px;border-radius:50%;background:var(--black);display:flex;align-items:center;justify-content:center">
        <span class="heading" style="font-size:32px;font-weight:700;color:var(--white);text-align:center;line-height:1.25">Timber<br>Ridge</span>
      </div>
    </div>
  </div>
  <h2 class="heading abs" style="left:617px;top:945px;font-size:46px;color:var(--green)">About Us</h2>
  <div class="rule abs" style="left:617px;top:1008px"></div>
  <p class="body-text abs" style="left:617px;top:1035px;width:440px">Timber Ridge is an elite baseball and softball training facility in Sacramento. We are committed to the development of these young athletes physically, mentally and emotionally on and off the field. We are here to train, guide and mentor the youth to become the best versions of themselves. Whether their sport takes them to the next level, Timber Ridge wants to see them thrive as human beings first above all else. We are committed to the development of these young athletes on and off the field, and we are here to train and guide the youth.</p>
  <a class="btn btn-solid abs" style="left:617px;top:1317px;width:168px;height:53px;font-size:16px">Read More</a>
</section>

<section class="abs" style="left:0;top:1470px;width:1200px;height:553px;overflow:hidden">
  <div class="abs" role="img" aria-label="Batting net with a softball in flight over a grass and dirt practice field" style="left:0;top:0;width:800px;height:553px;background:
    radial-gradient(ellipse 260px 300px at 120px 220px,rgba(20,22,18,.75),transparent 70%),
    radial-gradient(ellipse 180px 90px at 660px 70px,rgba(230,120,60,.45),transparent 70%),
    linear-gradient(180deg,#6e7d5a 0%,#86985f 30%,#9aae62 50%,#8fa558 62%,#c9b99a 80%,#d8c9ad 100%)"></div>
  <svg class="abs" style="left:0;top:0" width="1200" height="553" viewBox="0 0 1200 553">
    <polygon points="760,0 1200,0 1200,553 590,553" fill="#fff"/>
    <polygon points="773,0 1200,0 1200,553 617,553" fill="#3cf01c"/>
  </svg>
  <h2 class="heading abs" style="left:763px;top:88px;font-size:44px;color:var(--black)">Our Facility</h2>
  <div class="abs" style="left:763px;top:148px;width:56px;height:5px;background:var(--black)"></div>
  <p class="body-text abs" style="left:768px;top:172px;width:357px;color:var(--black)">Sed ut perspiciatis unde omnis iste natus error sit volu platem accusantium doloremque laudantium, totam rem aperiam, eaque ipsa quae ab illo inventore veritatis et quasi architecto beatae vitae dicta sunt explicabo. Nemo enim ipsam voluptatem quia voluptas sit aspernatur aut odit aut fugit, sed quia consequuntur magni dolores eos qui ratione voluptatem sequi nesciunt. Neque porro quisquam est, qui dolorem ipsum quia dolor sit amet, consectetur, adipisci tempora incidunt ut labore et dolore magnam..</p>
  <a class="btn abs" style="left:765px;top:436px;width:254px;height:52px;border:2px solid var(--black);color:var(--black);font-size:13.5px">Online Facility Schedule</a>
</section>

<h2 class="heading abs" style="left:0;width:1200px;top:2080px;text-align:center;font-size:48px;color:var(--green)">Our Team</h2>
<div class="rule abs" style="left:572px;top:2146px"></div>

<article class="team-card abs" style="left:112px">
  <div class="team-photo abs" role="img" aria-label="Portrait of a smiling coach with long blonde hair" style="background:
    radial-gradient(ellipse 110px 140px at 155px 130px,#e2b79a,transparent 75%),
    radial-gradient(ellipse 160px 190px at 155px 120px,#b99363,transparent 80%),
    radial-gradient(ellipse 200px 60px at 155px 280px,#1f2638,transparent 80%),
    linear-gradient(180deg,#f4f3f1,#e6e3de)"></div>
  <svg class="abs" style="left:0;top:218px" width="311" height="60"><polygon points="0,40 311,0 311,60 0,60" fill="#3cf01c"/><polygon points="0,48 311,8 311,60 0,60" fill="#1b1b1b"/></svg>
  <h3 class="team-name heading abs">Dana Whitford</h3>
  <p class="team-role abs">Owner of Timber Ridge, Director of Ridge Sparks 12u-18u, Private Hitting/Slapping/Fielding Coach</p>
</article>
<article class="team-card abs" style="left:446px">
  <div class="team-photo abs" role="img" aria-label="Portrait of a coach in a dark baseball cap" style="background:
    radial-gradient(ellipse 150px 60px at 155px 40px,#1c1c1c,transparent 80%),
    radial-gradient(ellipse 100px 130px at 155px 150px,#8a5a3c,transparent 75%),
    radial-gradient(ellipse 200px 60px at 155px 285px,#1e2230,transparent 80%),
    linear-gradient(180deg,#fafafa,#eeeeee)"></div>
  <svg class="abs" style="left:0;top:218px" width="311" height="60"><polygon points="0,40 311,0 311,60 0,60" fill="#3cf01c"/><polygon points="0,48 311,8 311,60 0,60" fill="#1b1b1b"/></svg>
  <h3 class="team-name heading abs">Curtis Ambrose</h3>
  <p class="team-role abs">Owner of Timber Ridge, Director of Ridge Sparks 12u-18u, Private Hitting/Slapping/Fielding Coach</p>
</article>
<article class="team-card abs" style="left:780px">
  <div class="team-photo abs" role="img" aria-label="Portrait of a smiling coach with brown hair" style="background:
    radial-gradient(ellipse 110px 140px at 170px 140px,#e0b08e,transparent 75%),
    radial-gradient(ellipse 180px 220px at 150px 130px,#6e4a2e,transparent 80%),
    linear-gradient(180deg,#efece8,#ddd6cc)"></div>
  <svg class="abs" style="left:0;top:218px" width="311" height="60"><polygon points="0,40 311,0 311,60 0,60" fill="#3cf01c"/><polygon points="0,48 311,8 311,60 0,60" fill="#1b1b1b"/></svg>
  <h3 class="team-name heading abs">Lena Castillo</h3>
  <p class="team-role abs">Born and raised in Roseville, CA. Lena played 1 complete season of collegiate baseball due to ill-timed injuries</p>
</article>

<h2 class="heading abs" style="left:0;width:1200px;top:2723px;text-align:center;font-size:48px;color:var(--green)">Camps/Classes</h2>
<div class="rule abs" style="left:572px;top:2790px"></div>

<article class="camp-card abs" style="left:112px;top:2843px">
  <div class="camp-photo abs" role="img" aria-label="Young players in the dugout wearing caps and gloves" style="background:
    radial-gradient(ellipse 70px 110px at 80px 120px,#3c4048,transparent 80%),
    radial-gradient(ellipse 60px 40px at 90px 30px,#f2f2f2,transparent 80%),
    linear-gradient(135deg,#e9ecee 0%,#b8bec4 55%,#6b5a48 100%)"></div>
  <h3 class="camp-title abs">Sed ut perspiciatis unde omnis iste natus</h3>
  <p class="camp-text abs">Nemo enim ipsam voluptatem quia vol uptas sit aspernatur aut odit aut fug consequuntur magni dolores....</p>
  <span class="camp-more abs">READ MORE</span>
</article>
<article class="camp-card abs" style="left:618px;top:2843px">
  <div class="camp-photo abs" role="img" aria-label="Softball resting in a leather glove on a tree stump" style="background:
    radial-gradient(circle 40px at 115px 90px,#d8ee3a,transparent 90%),
    radial-gradient(ellipse 100px 70px at 105px 85px,#8a5a34,transparent 85%),
    linear-gradient(180deg,#5a4a3c 0%,#7a5838 60%,#a07c58 100%)"></div>
  <h3 class="camp-title abs">Sed ut perspiciatis unde omnis iste natus</h3>
  <p class="camp-text abs">Nemo enim ipsam voluptatem quia vol uptas sit aspernatur aut odit aut fug consequuntur magni dolores....</p>
  <span class="camp-more abs">READ MORE</span>
</article>
<article class="camp-card abs" style="left:112px;top:3108px">
  <div class="camp-photo abs" role="img" aria-label="Ball field seen through chain-link fence at dusk" style="background:
    radial-gradient(ellipse 120px 40px at 105px 70px,rgba(255,230,180,.45),transparent 80%),
    linear-gradient(180deg,#3a3050 0%,#5a4a6a 30%,#4a5a48 50%,#3e7a34 75%,#2c5a24 100%)"></div>
  <h3 class="camp-title abs">Sed ut perspiciatis unde omnis iste natus</h3>
  <p class="camp-text abs">Nemo enim ipsam voluptatem quia vol uptas sit aspernatur aut odit aut fug consequuntur magni dolores....</p>
  <span class="camp-more abs">READ MORE</span>
</article>
<article class="camp-card abs" style="left:618px;top:3108px">
  <div class="camp-photo abs" role="img" aria-label="Worn baseballs on a dark surface" style="background:
    radial-gradient(circle 40px at 70px 150px,#cfc8bc,transparent 90%),
    radial-gradient(circle 38px at 140px 130px,#bdb5a8,transparent 90%),
    radial-gradient(circle 34px at 120px 50px,#a39a8c,transparent 90%),
    linear-gradient(135deg,#2a2622,#4a443e)"></div>
  <h3 class="camp-title abs">Sed ut perspiciatis unde omnis iste natus</h3>
  <p class="camp-text abs">Nemo enim ipsam voluptatem quia vol uptas sit aspernatur aut odit aut fug consequuntur magni dolores....</p>
  <span class="camp-more abs">READ MORE</span>
</article>

<section class="abs" style="left:0;top:3430px;width:1200px;height:555px;overflow:hidden">
  <div class="abs" role="img" aria-label="Baseball and leather glove lying on green grass" style="left:400px;top:0;width:800px;height:555px;background:
    radial-gradient(circle 95px at 460px 290px,#f1efe8,transparent 92%),
    radial-gradient(ellipse 170px 110px at 680px 200px,#7a4a2a,transparent 85%),
    radial-gradient(ellipse 500px 200px at 450px 120px,#b8d87a,transparent 75%),
    linear-gradient(180deg,#7ab83a 0%,#4f9a22 45%,#2e6a14 75%,#1a3e0a 100%)"></div>
  <svg class="abs" style="left:0;top:0" width="1200" height="555" viewBox="0 0 1200 555">
    <polygon points="0,0 460,0 615,555 0,555" fill="#fff"/>
    <polygon points="0,0 447,0 600,555 0,555" fill="#3cf01c"/>
  </svg>
  <h2 class="heading abs" style="left:76px;top:88px;font-size:44px;color:var(--black)">Lessons</h2>
  <div class="abs" style="left:76px;top:148px;width:56px;height:5px;background:var(--black)"></div>
  <p class="body-text abs" style="left:80px;top:172px;width:357px;color:var(--black)">Sed ut perspiciatis unde omnis iste natus error sit volu platem accusantium doloremque laudantium, totam rem aperiam, eaque ipsa quae ab illo inventore veritatis et quasi architecto beatae vitae dicta sunt explicabo. Nemo enim ipsam voluptatem quia voluptas sit aspernatur aut odit aut fugit, sed quia consequuntur magni dolores eos qui ratione voluptatem sequi nesciunt. Neque porro quisquam est, qui dolorem ipsum quia dolor sit amet, consectetur, adipisci tempora incidunt ut labore et dolore magnam..</p>
  <a class="btn abs" style="left:77px;top:440px;width:160px;height:53px;border:2px solid var(--black);color:var(--black);font-size:16px">Learn More</a>
</section>

<footer>
  <div class="brand abs" style="left:390px;top:4050px">
    <div class="brand-mark" style="width:92px;height:92px"></div>
    <div class="brand-name" style="font-size:31px">Timber Ridge<br><span style="font-size:14px;color:var(--green);letter-spacing:3px">Baseball and Softball</span></div>
  </div>
  <nav class="footer-nav nav abs">
    <span>Home</span><span>About Us</span><span>Our Facility</span><span>Lessons</span><span>Team Rental Pricing</span><span>Instructor Opportunities</span><span>Camps/Classes</span>
  </nav>
  <div class="divider abs" style="top:4225px"></div>
  <div class="contact abs" style="left:152px;top:4250px">
    <span class="contact-icon"><svg width="16" height="20" viewBox="0 0 16 20"><path d="M8 0a7 7 0 0 0-7 7c0 5 7 13 7 13s7-8 7-13a7 7 0 0 0-7-7zm0 10a3 3 0 1 1 0-6 3 3 0 0 1 0 6z" fill="#fff"/></svg></span>
    <span>2280 Cedar Mill Rd Suite #12<br>Pine Hollow, Ca 95999</span>
  </div>
  <div class="contact abs" style="left:545px;top:4250px">
    <span class="contact-icon"><svg width="18" height="18" viewBox="0 0 24 24"><path d="M6.6 10.8a15 15 0 0 0 6.6 6.6l2.2-2.2a1 1 0 0 1 1-.25 11.4 11.4 0 0 0 3.6.57 1 1 0 0 1 1 1V20a1 1 0 0 1-1 1A17 17 0 0 1 3 4a1 1 0 0 1 1-1h3.5a1 1 0 0 1 1 1c0 1.25.2 2.450.57 3.6a1 1 0 0 1-.25 1z" fill="#fff"/></svg></span>
    <span>555-014-2268</span>
  </div>
  <div class="contact abs" style="left:835px;top:4250px">
    <span class="contact-icon"><svg width="18" height="14" viewBox="0 0 18 14"><rect x="0" y="0" width="18" height="14" rx="2" fill="#fff"/><path d="M1 1l8 6 8-6" stroke="#000" stroke-width="1.6" fill="none"/></svg></span>
    <span>info@timberridge482.example</span>
  </div>
  <div class="divider abs" style="top:4330px"></div>
  <div class="abs" style="left:112px;top:4350px;display:flex;gap:10px">
    <span class="social"></span><span class="social"></span><span class="social"></span>
  </div>
  <p class="abs" style="left:834px;top:4362px;font-size:14px">© 2022 Northline Studio.All rights reserved &nbsp;&nbsp; C2</p>
</footer>

</body>
</html>
```